Designer Instructions – Updated Referral Program Flyer

(Based on the mock-up in “Brief Layout and Instructions.pdf”)

OVERALL STYLE + LAYOUT

Maintain the same general layout, structure, and flow as the mock-up flyer (front and back).

This is an update of an older flyer, not a full redesign — keep the same sections, proportions, and overall visual feel, but with cleaner, more modern design improvements.

The final flyer should look clean, bold, professional, and high-impact, geared toward realtors, property managers, and contractors who refer work.

FRONT SIDE INSTRUCTIONS
1. Header Section

Remove the Rebuild Harbor Crest logo from the top banner.
(Shown on page 1 of the PDF)

2. Main Headline

Keep the same three-line structure:
EARN
UNLIMITED
CASH

Center it, maximize impact, and increase the font size of CASH so all three words match in importance.

Make the headline bold, clean, and the main focal point.

3. Cash Incentive Box

Keep the "$500 minimum OR 10% per referral" box, but upgrade the graphics to look sharper and more modern.

Ensure the wording matches exactly what’s in the mock-up.

4. Premier Partner Program Ribbon

Clean up and modernize the "PREMIER PARTNER PROGRAM" bar while keeping the same position and structure.

Ensure the checkmark badge remains crisp and professional.

5. Supporting Icons Section

Keep the four icons/benefit boxes (Guaranteed Payout, Free Evaluations, Affordable Solutions, Industry Leaders) in the same order.

Update the icons to cleaner, more modern styles — but maintain the same meanings.

Improve alignment and spacing for sharper visual consistency.

6. Remove Icons in Contact Area

At the bottom (“CALL TEXT OR BOOK ONLINE 858-471-6093 BrightlaneRenovate.com”), remove the phone and internet icons, as noted on page 2 of the PDF.

7. Replace All Images

I (Dorian) will provide all updated stock images separately via email.

Replace the flood/water-damage imagery and roof leak with the new images I send.

Keep image placement and proportions the same as the mock-up.

BACK SIDE INSTRUCTIONS
1. Header Image + “REFER / EARN” Section

Maintain the same large split-image layout (“The more you refer, the more you earn”).

Replace all background imagery with the new assets I will send.

Keep the CASH FLOW image section but modernize the type and spacing.

2. “HOW IT WORKS” Section

Preserve the three-column layout:

Refer Flood, Water & Mold Damage

We Take Care of Everything (evaluations/insurance)

Get Paid to Share

Update images, tighten spacing, and use modern iconography.

3. Remove Phone/Internet Icons

Same as the front side — remove small communication icons and keep only the text/number/URL.

4. Bottom Contact Bar

Keep the blue bar, same wording, same layout — just modernize the style if needed for clarity.

5. Replace All Back-Side Images

Again, I will email you the image assets.

Keep the layout EXACT — just update with higher-quality photos and improved design.

TEXT CONTENT (Keep as-is unless spacing adjustments needed)

All text shown in the PDF should remain exactly the same unless spacing or visual balance requires minor adjustments.
Example from page 3:

“REFER FLOOD, MOLD & CONSTRUCTION JOBS”

“We Schedule a Free Estimate. If Approved, You Get Paid.”

“Everybody Benefits From Referrals”

Everything stays, just refreshed and visually improved.

DESIGN GOALS

Flyer should look high-end and trustworthy, not salesy.

Consistent color theme: blues, whites, yellows, same palette as original.

Use bold, modern fonts with strong readability.

Ensure all headlines pop and all benefit boxes are clean, well-aligned, and evenly spaced.

The final result should feel like a premium referral program flyer for a top-tier restoration/remodel company.

FILES I WILL PROVIDE

I will send the designer:

All replacement stock photos

Any updated logos (if needed)

Original high-resolution version of the mock-up (if available)

Any additional icons preferred

Colors
0054AA
0677BA
7BADD7
CADEEF
E8F1F8

Requirements
Must have
• Designer Instructions – Updated Referral Program Flyer (Based on the mock-up in “Brief Layout and Instructions.pdf”) OVERALL STYLE + LAYOUT Maintain the same general layout, structure, and flow as the mock-up flyer (front and back). This is an update of an older flyer, not a full redesign — keep the same sections, proportions, and overall visual feel, but with cleaner, more modern design improvements. The final flyer should look clean, bold, professional, and high-impact, geared toward realtors, property managers, and contractors who refer work. FRONT SIDE INSTRUCTIONS 1. Header Section Remove the Rebuild Harbor Crest logo from the top banner. (Shown on page 1 of the PDF) 2. Main Headline Keep the same three-line structure: EARN UNLIMITED CASH Center it, maximize impact, and increase the font size of CASH so all three words match in importance. Make the headline bold, clean, and the main focal point. 3. Cash Incentive Box Keep the "$500 minimum OR 10% per referral" box, but upgrade the graphics to look sharper and more modern. Ensure the wording matches exactly what’s in the mock-up. 4. Premier Partner Program Ribbon Clean up and modernize the "PREMIER PARTNER PROGRAM" bar while keeping the same position and structure. Ensure the checkmark badge remains crisp and professional. 5. Supporting Icons Section Keep the four icons/benefit boxes (Guaranteed Payout, Free Evaluations, Affordable Solutions, Industry Leaders) in the same order. Update the icons to cleaner, more modern styles — but maintain the same meanings. Improve alignment and spacing for sharper visual consistency. 6. Remove Icons in Contact Area At the bottom (“CALL TEXT OR BOOK ONLINE 858-471-6093 BrightlaneRenovate.com”), remove the phone and internet icons, as noted on page 2 of the PDF. 7. Replace All Images I (Dorian) will provide all updated stock images separately via email. Replace the flood/water-damage imagery and roof leak with the new images I send. Keep image placement and proportions the same as the mock-up. BACK SIDE INSTRUCTIONS 1. Header Image + “REFER / EARN” Section Maintain the same large split-image layout (“The more you refer, the more you earn”). Replace all background imagery with the new assets I will send. Keep the CASH FLOW image section but modernize the type and spacing. 2. “HOW IT WORKS” Section Preserve the three-column layout: Refer Flood, Water & Mold Damage We Take Care of Everything (evaluations/insurance) Get Paid to Share Update images, tighten spacing, and use modern iconography. 3. Remove Phone/Internet Icons Same as the front side — remove small communication icons and keep only the text/number/URL. 4. Bottom Contact Bar Keep the blue bar, same wording, same layout — just modernize the style if needed for clarity. 5. Replace All Back-Side Images Again, I will email you the image assets. Keep the layout EXACT — just update with higher-quality photos and improved design. TEXT CONTENT (Keep as-is unless spacing adjustments needed) All text shown in the PDF should remain exactly the same unless spacing or visual balance requires minor adjustments. Example from page 3: “REFER FLOOD, MOLD & CONSTRUCTION JOBS” “We Schedule a Free Estimate. If Approved, You Get Paid.” “Everybody Benefits From Referrals” Everything stays, just refreshed and visually improved. DESIGN GOALS Flyer should look high-end and trustworthy, not salesy. Consistent color theme: blues, whites, yellows, same palette as original. Use bold, modern fonts with strong readability. Ensure all headlines pop and all benefit boxes are clean, well-aligned, and evenly spaced. The final result should feel like a premium referral program flyer for a top-tier restoration/remodel company. FILES I WILL PROVIDE I will send the designer: All replacement stock photos Any updated logos (if needed) Original high-resolution version of the mock-up (if available) Any additional icons preferred

```html
<!DOCTYPE html>
<html lang="en">
<head>
<meta charset="utf-8">
<title>Premier Partner Referral Program Flyer</title>
<link href="https://fonts.googleapis.com/css2?family=Anton&family=Oswald:wght@300;400&family=Poppins:wght@500;600;700;800&display=swap" rel="stylesheet">
<style>
:root{
  --page:#d4d6d9;
  --navy:#1d4f87;
  --ink:#1f4a7a;
  --bar:#244a72;
  --royal:#1e64a8;
  --red:#d13a3d;
  --yellow:#f0d12e;
  --mist:#e4e5ea;
  --white:#ffffff;
  --deep:#0c2238;
  --mid:#235a8c;
}
*{margin:0;padding:0;box-sizing:border-box}
html,body{width:936px;height:1200px;overflow:hidden;background:var(--page)}
body{position:relative;font-family:"Poppins",sans-serif}
.card{position:absolute;left:122px;width:684px;height:442px;background:var(--white);overflow:hidden}
.card--front{top:104px}
.card--back{top:601px}
.abs{position:absolute}
svg{display:block}

/* front hero */
.hero-art{left:0;top:0}
.headline{left:0;top:26px;width:294px;text-align:center;font-weight:800;line-height:1;letter-spacing:-1px}
.headline span{display:block}
.headline .earn{color:var(--yellow);font-size:60px}
.headline .unlimited{color:var(--white);font-size:44px;margin:6px 0 4px}
.headline .cash{color:var(--yellow);font-size:60px}

/* offer band */
.band{left:0;top:223px}
.offer-amount{left:52px;top:230px;color:var(--white);font-weight:800;font-size:38px;line-height:1}
.offer-amount sup{font-size:17px;vertical-align:top;position:relative;top:2px}
.offer-label{color:var(--white);font-weight:700;font-size:14.5px;line-height:1}
.offer-label--min{left:69px;top:268px}
.offer-or{left:161px;top:243px;width:50px;height:34px;background:var(--yellow);color:var(--navy);font-weight:800;font-size:22px;display:flex;align-items:center;justify-content:center}
.offer-pct{left:224px;top:230px;color:var(--white);font-weight:800;font-size:38px;line-height:1}
.offer-label--per{left:224px;top:268px}
.ribbon-text{font-weight:700;line-height:1;text-align:center}
.ribbon-premier{left:340px;top:232px;width:300px;color:var(--navy);font-size:17px}
.ribbon-partner{left:370px;top:268px;width:110px;color:var(--white);font-size:15.5px}
.ribbon-program{left:530px;top:268px;width:110px;color:var(--white);font-size:15.5px}

/* benefits */
.benefits{left:0;top:300px;width:684px;height:104px;background:var(--mist)}
.tagline{position:absolute;left:0;width:684px;text-align:center;font-weight:700;font-size:12.5px;letter-spacing:3.2px;color:var(--ink)}
.tagline .hot{color:var(--red)}
.tagline--top{top:2px}
.tagline--bottom{top:87px}
.benefit{position:absolute;top:22px}
.benefit-icon{position:absolute;left:0;top:0}
.benefit-title{position:absolute;top:0;font-weight:500;font-size:12.5px;line-height:14px;color:var(--ink);white-space:nowrap}
.benefit-text{position:absolute;top:28px;left:0;font-weight:600;font-size:9.6px;line-height:12.5px;color:var(--ink);white-space:nowrap}
.benefit--payout{left:26px}
.benefit--eval{left:190px}
.benefit--afford{left:355px}
.benefit--leaders{left:518px}
.divider{position:absolute;top:26px;width:1px;height:50px;background:var(--ink)}

/* contact bar */
.contact{left:0;top:408px;width:684px;height:34px}
.contact-label{position:absolute;left:22px;top:9px;color:var(--white);font-weight:700;font-size:13.5px;line-height:1;white-space:nowrap}
.contact-label .soft{font-weight:500}
.contact-phone{position:absolute;left:272px;top:1px;color:var(--ink);font-weight:600;font-size:24px;line-height:32px;letter-spacing:.3px}
.contact-web{position:absolute;left:458px;top:10px;color:var(--ink);font-weight:600;font-size:12.2px;line-height:1}

/* back hero */
.back-art{left:0;top:0}
.slogan{left:58px;top:18px;width:130px;font-family:"Anton",sans-serif;line-height:.96;text-align:left}
.slogan span{display:block;transform-origin:left center}
.slogan .lead{color:var(--white);font-size:24px;transform:scaleX(.86)}
.slogan .big{font-size:56px;background:linear-gradient(180deg,#f7d72c 0%,#f3b33a 55%,#e9923b 100%);-webkit-background-clip:text;background-clip:text;color:transparent;transform:scaleX(.84)}
.slogan .big--earn{font-size:66px}

/* how it works */
.how{left:0;top:206px}
.how-title{left:38px;top:212px;font-weight:700;font-size:16px;letter-spacing:4.4px;color:var(--navy);line-height:1}
.how-title .hot{color:var(--red)}
.step{position:absolute;top:263px;width:194px;height:133px}
.step--refer{left:25px}
.step--estimate{left:242px}
.step--benefit{left:459px}
.step-photo{position:absolute;left:0;top:0;width:194px;height:84px}
.step-caption{position:absolute;left:0;top:84px;width:194px;height:49px}
.step-text{position:absolute;left:0;top:84px;width:194px;height:49px;display:flex;align-items:center;justify-content:center;text-align:center;font-family:"Oswald",sans-serif;font-weight:300;font-size:13.5px;line-height:18px;color:var(--white)}
</style>
</head>
<body>

<!-- FRONT -->
<section class="card card--front" aria-label="Referral program flyer, front">
  <svg class="abs hero-art" width="684" height="223" viewBox="0 0 684 223">
    <defs>
      <linearGradient id="roomTone" x1="0" y1="0" x2="0" y2="1">
        <stop offset="0" stop-color="#c9c3bb"/>
        <stop offset=".55" stop-color="#7fb4cc"/>
        <stop offset="1" stop-color="#b9bcbf"/>
      </linearGradient>
    </defs>
    <polygon points="335,0 684,0 684,223 335,223 294,105" fill="url(#roomTone)" role="img" aria-label="Photo of blue drying fans and dehumidifiers in a water-damaged basement"/>
    <polygon points="0,0 323,0 282,105 323,223 0,223" fill="var(--navy)"/>
  </svg>
  <h1 class="abs headline">
    <span class="earn">EARN</span>
    <span class="unlimited">UNLIMITED</span>
    <span class="cash">CASH</span>
  </h1>

  <svg class="abs band" width="684" height="77" viewBox="0 0 684 77">
    <polygon points="20,6 172,6 197,70 38,70" fill="var(--red)"/>
    <polygon points="20,70 38,70 29,46" fill="var(--yellow)"/>
    <polygon points="172,6 330,6 349,70 197,70" fill="var(--royal)"/>
    <polygon points="331,6 638,6 646,32 340,32" fill="var(--yellow)"/>
    <polygon points="340,32 500,32 500,70 355,70" fill="var(--red)"/>
    <polygon points="500,32 646,32 664,70 500,70" fill="var(--royal)"/>
    <path d="M500 32 L514 38 L514 53 Q514 64 500 70 Q486 64 486 53 L486 38 Z" fill="var(--yellow)"/>
    <path d="M493 50 L499 56 L508 44" fill="none" stroke="var(--royal)" stroke-width="3" stroke-linecap="round" stroke-linejoin="round"/>
  </svg>
  <div class="abs offer-amount"><sup>$</sup>500</div>
  <div class="abs offer-label offer-label--min">MINIMUM</div>
  <div class="abs offer-or">OR</div>
  <div class="abs offer-pct">10%</div>
  <div class="abs offer-label offer-label--per">PER REFERRAL</div>
  <div class="abs ribbon-text ribbon-premier">PREMIER</div>
  <div class="abs ribbon-text ribbon-partner">PARTNER</div>
  <div class="abs ribbon-text ribbon-program">PROGRAM</div>

  <div class="abs benefits">
    <p class="tagline tagline--top"><span class="hot">PARTNER WITH US</span> &amp; EVERYBODY WINS!</p>

    <div class="benefit benefit--payout">
      <svg class="benefit-icon" width="24" height="24" viewBox="0 0 24 24">
        <circle cx="12" cy="12" r="11" fill="var(--navy)"/>
        <circle cx="12" cy="12" r="7" fill="none" stroke="var(--white)" stroke-width="1.4"/>
        <text x="12" y="16" text-anchor="middle" font-family="Poppins,sans-serif" font-weight="700" font-size="11" fill="var(--white)">$</text>
      </svg>
      <p class="benefit-title" style="left:28px">GUARANTEED<br>PAYOUT</p>
      <p class="benefit-text">Minimum $500 or 10%<br>of Total Invoice Paid Fast</p>
    </div>
    <span class="divider" style="left:168px"></span>

    <div class="benefit benefit--eval">
      <svg class="benefit-icon" width="20" height="24" viewBox="0 0 20 24">
        <rect x="1" y="1" width="18" height="22" rx="2.5" fill="var(--navy)"/>
        <path d="M5 8h10M5 12h10M5 16h7" stroke="var(--white)" stroke-width="1.6" stroke-linecap="round"/>
      </svg>
      <p class="benefit-title" style="left:28px">FREE<br>EVALUATIONS</p>
      <p class="benefit-text">Fast &amp; Free Inspections<br>and Written Estimates</p>
    </div>
    <span class="divider" style="left:327px"></span>

    <div class="benefit benefit--afford">
      <svg class="benefit-icon" width="24" height="24" viewBox="0 0 24 24">
        <circle cx="12" cy="12" r="11" fill="var(--navy)"/>
        <text x="10" y="16.5" text-anchor="middle" font-family="Poppins,sans-serif" font-weight="700" font-size="12" fill="var(--white)">$</text>
        <path d="M17 7v9M14.5 13.5 17 16l2.5-2.5" fill="none" stroke="var(--white)" stroke-width="1.5" stroke-linecap="round" stroke-linejoin="round"/>
      </svg>
      <p class="benefit-title" style="left:28px">AFFORDABLE<br>SOLUTIONS</p>
      <p class="benefit-text">Lowest Out of Pocket<br>Costs for Your Customers</p>
    </div>
    <span class="divider" style="left:500px"></span>

    <div class="benefit benefit--leaders">
      <svg class="benefit-icon" width="26" height="24" viewBox="0 0 26 24">
        <circle cx="10" cy="7" r="5" fill="var(--navy)"/>
        <path d="M1 22c0-6 4-9 9-9s9 3 9 9z" fill="var(--navy)"/>
        <circle cx="20" cy="15" r="5" fill="var(--navy)" stroke="var(--mist)" stroke-width="1.2"/>
        <path d="M17.8 15l1.6 1.6 2.8-3" fill="none" stroke="var(--white)" stroke-width="1.4" stroke-linecap="round" stroke-linejoin="round"/>
      </svg>
      <p class="benefit-title" style="left:27px">INDUSTRY<br>LEADERS</p>
      <p class="benefit-text">Licensed &amp; Certified Experts<br>Provide 100% Guarantee</p>
    </div>

    <p class="tagline tagline--bottom">SEND <span class="hot">REFERRALS</span>. GET <span class="hot">PAID</span>. GROW <span class="hot">YOUR BUSINESS</span></p>
  </div>

  <div class="abs contact">
    <svg class="abs" style="left:0;top:0" width="260" height="34" viewBox="0 0 260 34">
      <polygon points="0,0 249,0 260,34 0,34" fill="var(--bar)"/>
    </svg>
    <p class="contact-label">CALL, TEXT <span class="soft">OR</span> BOOK ONLINE</p>
    <p class="contact-phone">858-471-6093</p>
    <p class="contact-web">WWW.BRIGHTLANERENOVATE.COM</p>
  </div>
</section>

<!-- BACK -->
<section class="card card--back" aria-label="Referral program flyer, back">
  <svg class="abs back-art" width="684" height="206" viewBox="0 0 684 206">
    <defs>
      <linearGradient id="moneyTone" x1="0" y1="0" x2="1" y2="1">
        <stop offset="0" stop-color="#d9ddd6"/>
        <stop offset=".5" stop-color="#a9c9cf"/>
        <stop offset="1" stop-color="#c8cdc6"/>
      </linearGradient>
    </defs>
    <rect width="684" height="206" fill="var(--mid)"/>
    <polygon points="60,0 200,0 168,206 0,206 0,129" fill="var(--deep)"/>
    <polygon points="194,0 322,0 284,91" fill="var(--red)"/>
    <polygon points="322,0 684,0 684,206 194,206 284,91" fill="url(#moneyTone)" role="img" aria-label="Photo of hundred-dollar bills with letter tiles spelling CASH FLOW"/>
  </svg>
  <h2 class="abs slogan">
    <span class="lead">THE MORE YOU</span>
    <span class="big">REFER</span>
    <span class="lead">THE MORE YOU</span>
    <span class="big big--earn">EARN</span>
  </h2>

  <svg class="abs how" width="684" height="33" viewBox="0 0 684 33">
    <polygon points="0,0 265,0 250,33 0,33" fill="var(--yellow)"/>
    <polygon points="283,0 305,0 290,33 268,33" fill="var(--yellow)"/>
    <polygon points="323,0 345,0 330,33 308,33" fill="var(--yellow)"/>
    <polygon points="363,0 385,0 370,33 348,33" fill="var(--yellow)"/>
    <polygon points="403,0 425,0 410,33 388,33" fill="var(--yellow)"/>
    <polygon points="443,0 465,0 450,33 428,33" fill="var(--yellow)"/>
    <polygon points="483,0 505,0 490,33 468,33" fill="var(--yellow)"/>
    <polygon points="523,0 545,0 530,33 508,33" fill="var(--yellow)"/>
    <polygon points="563,0 585,0 570,33 548,33" fill="var(--yellow)"/>
    <polygon points="603,0 625,0 610,33 588,33" fill="var(--yellow)"/>
    <polygon points="643,0 684,0 684,33 628,33" fill="var(--yellow)"/>
  </svg>
  <p class="abs how-title"><span class="hot">HOW</span> IT WORKS</p>

  <div class="step step--refer">
    <div class="step-photo" role="img" aria-label="Photo of a leaking white pipe under a sink" style="background:linear-gradient(135deg,#3a3a3a,#d8d8d8 60%,#555)"></div>
    <svg class="step-caption" width="194" height="49" viewBox="0 0 194 49"><polygon points="0,0 194,0 194,33 179,49 0,49" fill="var(--bar)"/></svg>
    <p class="step-text">Refer Flood, Mold &amp;<br>Construction Jobs</p>
  </div>
  <div class="step step--estimate">
    <div class="step-photo" role="img" aria-label="Photo of an inspector with a tablet in front of a house" style="background:linear-gradient(180deg,#cfd8e0,#e9ecec 55%,#6f8f4c)"></div>
    <svg class="step-caption" width="194" height="49" viewBox="0 0 194 49"><polygon points="0,0 194,0 194,33 179,49 0,49" fill="var(--bar)"/><polygon points="0,33 0,49 -1,49" fill="var(--bar)"/></svg>
    <p class="step-text">We Schedule a Free Estimate.<br>If Approved, You Get Paid.</p>
  </div>
  <div class="step step--benefit">
    <div class="step-photo" role="img" aria-label="Photo of a yellow road sign reading Get Paid to Share against a blue sky" style="background:linear-gradient(180deg,#3a7fc1,#a9cbe8 70%,#e5eef5)"></div>
    <svg class="step-caption" width="194" height="49" viewBox="0 0 194 49"><polygon points="0,0 194,0 194,33 179,49 0,49" fill="var(--bar)"/></svg>
    <p class="step-text">Everybody Benefits<br>From Referrals</p>
  </div>

  <div class="abs contact">
    <svg class="abs" style="left:0;top:0" width="260" height="34" viewBox="0 0 260 34">
      <polygon points="0,0 249,0 260,34 0,34" fill="var(--bar)"/>
    </svg>
    <p class="contact-label">CALL, TEXT <span class="soft">OR</span> BOOK ONLINE</p>
    <p class="contact-phone">858-471-6093</p>
    <p class="contact-web">WWW.BRIGHTLANERENOVATE.COM</p>
  </div>
</section>

</body>
</html>
```